Calm and Clear Wellness Flyer (new business startup)

One page...clear enough to be read if faxed. This mental health clinic treats depression/anxiety in kids and adults. It also treats opiate and alcohol addiction. It's in downtown Elmira, NY and the owner of the clinic is from Elmira NY, where it's located. This clinic does not take health insurance, so it charges a low rate of $75 a visit once they pay the $125 starting fee.
Updates

Target Market(s)

doctors offices, new patients

Industry/Entity Type

Doctor

Requirements
Must have
• see microsoft word document. pdf is printed on the company letterhead.
Nice to have
• a simplified map would be nice. if you can include the building it would be a plus. The same two fonts were used in the business cards and letter head (kennedy small caps boo*) and Refrigerator Delux.

```html
<!DOCTYPE html>
<html lang="en">
<head>
<meta charset="utf-8">
<title>Calm and Clear Wellness Flyer</title>
<link rel="stylesheet" href="https://fonts.googleapis.com/css2?family=Cormorant+SC:wght@500&family=Roboto+Condensed:wght@400;700&family=Roboto:wght@400;700&display=swap">
<style>
  :root {
    --orange: #f26a36;
    --blue: #27a9e1;
    --ink: #2b2b2b;
    --white: #ffffff;
    --brick: #8a4a34;
    --sky: #8ec4ea;
    --map: #eceeef;
  }
  * { box-sizing: border-box; margin: 0; padding: 0; }
  html, body { width: 1023px; height: 1200px; overflow: hidden; background: var(--white); }
  .flyer {
    width: 1023px; height: 1200px; display: flex; flex-direction: column;
    font-family: "Roboto Condensed", "Arial Narrow", sans-serif; color: var(--ink);
  }
  .brand {
    height: 150px; flex: none; display: flex; align-items: center; justify-content: center; gap: 18px;
  }
  .brand-dot { width: 60px; height: 60px; border-radius: 50%; background: var(--orange); }
  .brand-name { font-weight: 700; font-size: 48px; color: var(--orange); letter-spacing: 0.5px; }
  .provider-band {
    flex: none; background: var(--blue); color: var(--white); text-align: center; padding: 12px 0 14px;
  }
  .provider-name {
    font-family: "Cormorant SC", "Times New Roman", serif; font-weight: 500;
    font-size: 60px; line-height: 1;
  }
  .provider-title { font-size: 32px; letter-spacing: 4.5px; font-weight: 700; margin-top: 4px; }
  .call {
    text-align: center; color: var(--orange); font-weight: 700; font-size: 76px;
    line-height: 1; margin: 14px 0 10px;
  }
  .price-box {
    margin: 0 75px; background: var(--orange); color: var(--white); border-radius: 3px;
    padding: 10px 0 12px 38px; font-weight: 700; font-size: 40px; line-height: 1.2;
  }
  .price-row { display: flex; }
  .price-label { width: 670px; }
  .price-value { width: 150px; text-align: right; }
  .hours { text-align: center; font-size: 35px; margin: 10px 0 4px; }
  .conditions-head {
    display: flex; align-items: center; justify-content: center; gap: 8px;
    color: var(--orange); font-weight: 700; font-size: 40px; line-height: 1.1;
  }
  .conditions-head::before, .conditions-head::after {
    content: ""; width: 115px; height: 1.5px; background: var(--ink);
  }
  .conditions {
    text-align: center; font-family: "Roboto", Arial, sans-serif; font-size: 32px; line-height: 1.3;
    margin-top: 4px;
  }
  .sep {
    display: inline-block; width: 14px; height: 14px; border-radius: 50%;
    background: var(--orange); margin: 0 6px; vertical-align: middle;
  }
  .note {
    text-align: center; font-family: "Roboto", Arial, sans-serif; font-size: 19px;
    line-height: 1.3; margin: 12px 60px 0;
  }
  .tagline {
    text-align: center; font-family: "Roboto", Arial, sans-serif; font-weight: 700;
    font-size: 30px; margin: 10px 0 12px;
  }
  .visuals { flex: none; display: flex; gap: 16px; margin: 0 53px; height: 200px; }
  .building, .map { flex: 1; border: 1.5px solid var(--ink); }
  .building { background: linear-gradient(180deg, var(--sky) 0 18%, var(--brick) 18% 100%); }
  .map { background: linear-gradient(160deg, var(--map), #dfe4e8); }
  .substance {
    flex: none; margin: 6px 53px 0; background: var(--orange); color: var(--white); text-align: center;
    font-family: "Roboto", Arial, sans-serif; font-weight: 700; font-size: 21px;
    line-height: 1.25; padding: 8px 0;
  }
  .substance strong { font-size: 24px; }
  .footer {
    flex: none; margin-top: auto; background: var(--blue); color: var(--white); height: 56px;
    display: flex; align-items: center; justify-content: center; gap: 10px;
    font-family: "Roboto", Arial, sans-serif; font-size: 23px;
  }
  .footer svg { width: 22px; height: 22px; fill: var(--white); }
</style>
</head>
<body>
<main class="flyer">
  <header class="brand">
    <span class="brand-dot"></span>
    <span class="brand-name">CALM AND CLEAR WELLNESS</span>
  </header>

  <section class="provider-band">
    <h1 class="provider-name">DANIEL REYES, RPA, PLLC</h1>
    <p class="provider-title">Psychiatric Physician Assistant (PA-C-CAQ)</p>
  </section>

  <p class="call">CALL US :&nbsp; 607-555-0142</p>

  <section class="price-box">
    <div class="price-row"><span class="price-label">Psychiatric Evaluation &nbsp;(45min) -</span><span class="price-value">$125*</span></div>
    <div class="price-row"><span class="price-label">Psychiatric Office Visit (15min) -</span><span class="price-value">$75*</span></div>
    <div>AGES:&nbsp; 6 YEARS OLD AND UP</div>
  </section>

  <p class="hours">Hours:&nbsp; Monday &amp; Saturdays 9-4 pm</p>

  <h2 class="conditions-head">CONDITIONS TREATED</h2>
  <p class="conditions">
    Depression<span class="sep"></span>Anxiety<span class="sep"></span>PTSD<span class="sep"></span>ADHD<span class="sep"></span>Addiction<br>
    Bipolar<span class="sep"></span>Childhood Mood Disorders
  </p>

  <p class="note">*Although we do not partner with any Health Insurance Companies at this time, a bill will be<br>provided to you at the time of service for you to submit to your insurance company.</p>

  <p class="tagline">We work for you, not the insurance companies</p>

  <section class="visuals">
    <div class="building" role="img" aria-label="Photo of the downtown brick office building"></div>
    <div class="map" role="img" aria-label="Street map of downtown Millbrook with the clinic location marked"></div>
  </section>

  <p class="substance">Calm and Clear Wellness also treats substance use<br>disorders, including <strong>Opiates, Benzodiazepines, and Alcohol.</strong></p>

  <footer class="footer">
    <span>240 W. Water #12, Millbrook, NY 14990</span>
    <svg viewBox="0 0 24 24" aria-hidden="true"><path d="M6.6 10.8a15 15 0 0 0 6.6 6.6l2.2-2.2a1 1 0 0 1 1-.25 11.4 11.4 0 0 0 3.6.57 1 1 0 0 1 1 1V20a1 1 0 0 1-1 1A17 17 0 0 1 3 4a1 1 0 0 1 1-1h3.5a1 1 0 0 1 1 1c0 1.25.2 2.45.57 3.6a1 1 0 0 1-.25 1z"/></svg>
    <span>607-555-0142</span>
    <svg viewBox="0 0 24 24" aria-hidden="true"><path d="M6 2h10l2 2v5H6zM4 10h16a2 2 0 0 1 2 2v6h-4v4H6v-4H2v-6a2 2 0 0 1 2-2zm4 6v4h8v-4z"/></svg>
    <span>607-555-0187</span>
  </footer>
</main>
</body>
</html>
```